Web design project for exciting Australian start-up

Background
We are looking for a creative and talented web design artist to work alongside our market leading web developer.
• You will be required to create a modern and clean design theme for our website, incorporating selected rustic colour scheme elements for our exciting Australian start-up to operate within the coffee industry.
reoccurring work to be expected to flow to the successful designer.
Requirements
• c. 5 - 10 page website
• Landing page
• Log in/ out
• 404 template
• Typography is emphasised
• Please use either a) typemarrow.com, b) free web fonts, c) brindle fonts
• All design elements in vector format
• Preferably with icons for each header title(i.e. about us, how it works etc) but designer have free reign over how the site looks, so might not be applicable
• All pages to be responsive
• Down to eSlab resolution

High level visual design brief attached - additional pages to be worked from base design.

Design inspiration
• We would like to use design elements from the following sources:
http://www.zandrix.com/halcyon/ (Functionality)
Colour scheme refer to logo and complementary style guide

```html
<!DOCTYPE html>
<html lang="en">
<head>
<meta charset="utf-8">
<title>Brewhaven – Marketplace</title>
<link rel="stylesheet" href="https://fonts.googleapis.com/css2?family=Open+Sans:wght@400;600;700&family=Raleway:wght@300;400&display=swap">
<style>
:root{
  --cream:#f1efe2;
  --red:#e8413c;
  --brick:#c8262a;
  --orange:#b5590f;
  --amber:#f6a04d;
  --dark:#3d3d3d;
  --ink:#2d2d2d;
  --grey:#888;
  --line:#dcdcdc;
  --star:#f7b500;
  --footer-dark:#282828;
}
*{box-sizing:border-box;margin:0;padding:0}
html,body{width:1200px;height:1101px;overflow:hidden}
body{position:relative;background:#fff;font-family:"Open Sans",Arial,sans-serif;color:var(--ink)}
.abs{position:absolute}
.site-header{left:0;top:0;width:1200px;height:127px;background:var(--cream);border-bottom:3px solid var(--red)}
.brand{left:100px;top:42px;display:flex;align-items:center;gap:12px;font-weight:700;font-size:30px;color:var(--ink)}
.brand-mark{width:30px;height:30px;border-radius:50%;background:var(--brick)}
.account-nav{right:146px;top:47px;display:flex;gap:6px}
.account-nav a{display:block;height:28px;line-height:28px;padding:0 11px;border-radius:3px;color:#fff;font-size:13px;font-weight:600;text-decoration:none}
.btn-account{background:var(--dark)}
.btn-status{background:var(--amber);color:#3a2200!important}
.btn-logout{background:var(--red)}
.page-title{left:101px;top:158px;font-family:"Raleway",sans-serif;font-weight:300;font-size:31px;color:var(--red)}
.market-panel{left:101px;top:217px;width:998px;height:554px;border:1px solid var(--line);background:#f6f6f6;border-radius:2px}
.tabs{left:0;top:0;width:996px;height:48px;background:linear-gradient(#f3f3f3,#e6e6e6);border-bottom:1px solid var(--line);font-size:15px}
.tabs span{position:absolute;top:14px}
.label{color:var(--orange);font-weight:600}
.tab-active{left:175px;top:0!important;width:74px;height:48px;background:#f6f6f6;color:var(--orange);text-align:center;line-height:48px}
.search-bar{left:14px;top:60px;width:970px;height:50px;background:#fff;border:1px solid var(--line);font-size:14px}
.search-bar .cell{position:absolute;top:0;height:48px;line-height:48px;border-right:1px solid var(--line);padding-left:20px}
.sort{right:146px;top:10px;width:142px;height:30px;background:#eee;border:1px solid #ddd;border-radius:2px;padding-left:10px;line-height:28px;font-size:14px}
.view{right:7px;top:7px;width:86px;height:34px;background:#eee;border:1px solid #ddd;border-radius:2px}
.results-title{left:12px;top:128px;font-family:"Raleway",sans-serif;font-weight:400;font-size:25px;color:var(--red)}
.card{left:14px;width:970px;height:175px;background:linear-gradient(#fff 60%,#f4f4f4);border:1px solid var(--line)}
.card .seller{left:0;top:0;width:220px;height:173px;border-right:1px solid var(--line);display:flex;align-items:center;justify-content:center;font-weight:700;font-size:19px;color:var(--brick);text-align:center}
.card .info{left:238px;top:24px;font-size:13.5px;line-height:23px}
.card .reviews{left:632px;top:0;width:336px;height:173px;border-left:1px solid var(--line)}
.red{color:var(--brick);font-size:14.5px;margin-bottom:12px}
.muted{color:var(--grey)}
.row span:first-child{display:inline-block;width:113px}
.stars{left:179px;top:60px}
.site-footer{left:0;top:807px;width:1200px;height:220px;background:var(--cream)}
.fcol{top:20px}
.fcol h3{font-weight:400;font-size:16px;color:var(--brick);margin-bottom:8px}
.fcol li{list-style:none;font-size:12.5px;line-height:23px;color:#444}
.field{width:228px;height:29px;border:1px solid #ccc;background:#f6f6f6;font-size:12px;padding-left:16px;line-height:27px;margin-bottom:14px}
.submit{margin-left:157px;width:71px;height:29px;background:linear-gradient(#888,#555);color:#fff;font-size:13px;font-weight:600;text-align:center;line-height:29px;border-radius:2px}
.social li{display:flex;align-items:center;gap:8px;height:40px;font-size:12.5px;color:#888}
.social i{display:block;width:28px;height:28px;background:#7a93b8;border-radius:2px}
.social b{font-weight:400;font-size:15px;color:#2d5c9a}
.copyright{left:0;top:1027px;width:1200px;height:74px;background:var(--footer-dark);color:#aaa;font-size:14px;text-align:center;line-height:74px}
</style>
</head>
<body>
<header class="site-header abs">
  <div class="brand abs"><span class="brand-mark"></span><span>Brewhaven</span></div>
  <nav class="account-nav abs">
    <a class="btn-account" href="#">MY ACCOUNT</a><a class="btn-status" href="#">LOGGED IN</a><a class="btn-logout" href="#">LOG OUT</a>
  </nav>
</header>

<h1 class="page-title abs">MARKETPLACE</h1>

<section class="market-panel abs">
  <div class="tabs abs">
    <span class="label" style="left:20px">TENDER FORMAT :</span>
    <span class="tab-active abs">ALL</span>
    <span style="left:267px">ONE-OFF</span>
    <span style="left:374px">RECURRING</span>
    <span class="label" style="left:749px">QUANTITY (KG) :</span>
    <span style="left:884px">35 KG/WEEK</span>
  </div>
  <div class="search-bar abs">
    <div class="cell" style="left:0;width:220px"><span class="muted">✖</span>&nbsp;&nbsp; Results for Café Lumen</div>
    <div class="cell" style="left:220px;width:152px">
      <svg width="16" height="16" viewBox="0 0 24 24" style="vertical-align:-2px"><path fill="var(--star)" d="M12 2l3 7h7l-5.5 4.5 2 7.5-6.5-4.5-6.5 4.5 2-7.5L2 9h7z"/></svg>&nbsp; Save search</div>
    <span class="abs" style="right:300px;top:14px;color:#555">Sort :</span>
    <div class="sort abs">Highest rated <span style="position:absolute;right:8px;color:#777">▾</span></div>
    <span class="abs" style="right:100px;top:14px;color:#555">View :</span>
    <div class="view abs">
      <svg width="84" height="32" viewBox="0 0 84 32"><g fill="#555">
        <rect x="11" y="11" width="4" height="4"/><rect x="17" y="11" width="4" height="4"/><rect x="11" y="17" width="4" height="4"/><rect x="17" y="17" width="4" height="4"/>
        <rect x="36" y="11" width="3" height="3"/><rect x="40" y="11" width="3" height="3"/><rect x="44" y="11" width="3" height="3"/><rect x="36" y="15" width="3" height="3"/><rect x="40" y="15" width="3" height="3"/><rect x="44" y="15" width="3" height="3"/><rect x="36" y="19" width="3" height="3"/><rect x="40" y="19" width="3" height="3"/><rect x="44" y="19" width="3" height="3"/>
        <rect x="61" y="11" width="12" height="2"/><rect x="61" y="15" width="12" height="2"/><rect x="61" y="19" width="12" height="2"/></g></svg>
    </div>
  </div>
  <h2 class="results-title abs">RESULTS</h2>

  <article class="card abs" style="top:168px">
    <div class="seller abs">Marlow Roasters</div>
    <div class="info abs">
      <p class="red">Coffee bean XX</p>
      <p class="muted">Blend description :</p>
      <p class="row"><span>Origin</span>:&nbsp; [xx]</p>
      <p class="row"><span>Grind availability</span>:&nbsp; [xx]</p>
    </div>
    <div class="reviews abs">
      <p class="red abs" style="left:18px;top:24px">Reviews for this bean :</p>
      <p class="muted abs" style="left:19px;top:54px;font-size:13px;line-height:19px">Wholesaler's overall<br>customer rating :</p>
      <svg class="stars abs" width="118" height="24" viewBox="0 0 118 24"><defs><path id="st" d="M12 3l2.6 5.6 6.1.6-4.6 4.1 1.3 6-5.4-3.1-5.4 3.1 1.3-6-4.6-4.1 6.1-.6z"/></defs>
        <g><rect x="1" y="1" width="22" height="22" rx="3" fill="var(--star)"/><use href="#st" fill="#fff"/></g>
        <g transform="translate(24)"><rect x="1" y="1" width="22" height="22" rx="3" fill="var(--star)"/><use href="#st" fill="#fff"/></g>
        <g transform="translate(48)"><rect x="1" y="1" width="22" height="22" rx="3" fill="var(--star)"/><use href="#st" fill="#fff"/></g>
        <g transform="translate(72)"><rect x="1" y="1" width="22" height="22" rx="3" fill="var(--star)"/><use href="#st" fill="#fff"/></g>
        <g transform="translate(96)"><rect x="1" y="1" width="22" height="22" rx="3" fill="#ccc"/><use href="#st" fill="#fff"/></g></svg>
      <p class="muted abs" style="left:19px;top:116px;font-size:13px">Other offerings</p>
      <svg class="abs" style="left:135px;top:110px" width="160" height="34" viewBox="0 0 160 34"><g fill="#444">
        <path d="M3 14h20v8a7 7 0 0 1-7 7h-6a7 7 0 0 1-7-7z"/><path d="M23 16h3a3 3 0 0 1 0 6h-3" fill="none" stroke="#444" stroke-width="2"/><rect x="0" y="30" width="28" height="3" rx="1.5"/>
        <path d="M46 16l14-6 14 6-14 6z"/><path d="M51 19v6c4 3 14 3 18 0v-6l-9 4z"/><rect x="71" y="17" width="1.5" height="12"/>
        <path d="M94 8h16l-2 24h-12z"/><rect x="93" y="5" width="18" height="4" rx="1"/><circle cx="102" cy="18" r="3" fill="#fff"/>
        <path d="M130 14h5l12-7v22l-12-7h-5z"/><rect x="132" y="22" width="4" height="7"/></g></svg>
    </div>
  </article>

  <article class="card abs" style="top:356px">
    <div class="seller abs" style="color:#5a8a2a">Fernleaf Coffees</div>
    <div class="info abs">
      <p class="red">Coffee bean XX</p>
      <p class="muted">Blend description :</p>
      <p class="row"><span>Origin</span>:&nbsp; [xx]</p>
      <p class="row"><span>Grind availability</span>:&nbsp; [xx]</p>
    </div>
    <div class="reviews abs">
      <p class="red abs" style="left:18px;top:24px">Reviews for this bean :</p>
      <p class="muted abs" style="left:19px;top:54px;font-size:13px;line-height:19px">Wholesaler's overall<br>customer rating :</p>
      <svg class="stars abs" width="118" height="24" viewBox="0 0 118 24">
        <g><rect x="1" y="1" width="22" height="22" rx="3" fill="var(--star)"/><use href="#st" fill="#fff"/></g>
        <g transform="translate(24)"><rect x="1" y="1" width="22" height="22" rx="3" fill="var(--star)"/><use href="#st" fill="#fff"/></g>
        <g transform="translate(48)"><rect x="1" y="1" width="22" height="22" rx="3" fill="var(--star)"/><use href="#st" fill="#fff"/></g>
        <g transform="translate(72)"><rect x="1" y="1" width="22" height="22" rx="3" fill="var(--star)"/><use href="#st" fill="#fff"/></g>
        <g transform="translate(96)"><rect x="1" y="1" width="22" height="22" rx="3" fill="#ccc"/><use href="#st" fill="#fff"/></g></svg>
      <p class="muted abs" style="left:19px;top:116px;font-size:13px">Other offerings</p>
      <svg class="abs" style="left:135px;top:110px" width="160" height="34" viewBox="0 0 160 34"><g fill="#444">
        <path d="M3 14h20v8a7 7 0 0 1-7 7h-6a7 7 0 0 1-7-7z"/><path d="M23 16h3a3 3 0 0 1 0 6h-3" fill="none" stroke="#444" stroke-width="2"/><rect x="0" y="30" width="28" height="3" rx="1.5"/>
        <path d="M46 16l14-6 14 6-14 6z"/><path d="M51 19v6c4 3 14 3 18 0v-6l-9 4z"/><rect x="71" y="17" width="1.5" height="12"/>
        <path d="M94 8h16l-2 24h-12z"/><rect x="93" y="5" width="18" height="4" rx="1"/><circle cx="102" cy="18" r="3" fill="#fff"/>
        <path d="M130 14h5l12-7v22l-12-7h-5z"/><rect x="132" y="22" width="4" height="7"/></g></svg>
    </div>
  </article>
</section>

<footer class="site-footer abs">
  <div class="fcol abs" style="left:143px"><h3>Helpful info</h3><ul><li>About us</li><li>Media enquiries</li><li>Terms &amp; conditions</li><li>Privacy policy</li></ul></div>
  <div class="fcol abs" style="left:342px"><h3>Who we are</h3><ul><li>How it works</li><li>FAQ</li><li>Contact us</li></ul></div>
  <div class="fcol abs" style="left:551px"><h3>Email Signup</h3>
    <div class="field" style="margin-top:12px">Name</div><div class="field">Email ID</div><div class="submit">SUBMIT</div></div>
  <div class="fcol abs" style="left:860px"><h3>Connect with us</h3>
    <ul class="social">
      <li><i></i>Join with us on <b>Gatherly</b></li>
      <li><i style="background:#5bb8df"></i>Follow us on <b style="color:#2fa3d6">Chirpnet</b></li>
      <li><i style="background:#2a6fa8"></i>Share on <b style="color:#1e6aa5">Workweb</b></li>
      <li><i style="background:#c4362f"></i>Watch on <b style="color:#8a1e1a">Reelhub</b></li>
    </ul></div>
</footer>
<div class="copyright abs">Copyright © 2014 Brewhaven.&nbsp;&nbsp; All rights reserved.</div>
</body>
</html>
```